Professional BIO Template with photo and logo

Hello,
I need a professional Bio template developed via Microsoft WORD ASAP!!!!! I would like to just be able to add the text I need to add. So resize-able text boxes. Potentially able to adjust the font. These are the things I need added it to include.
Head shot (attached)
Text Box for Name
Text Box for phone number
Text box for email
KVT Logo (attached)
Maybe a blue banner at the top or some background boxes that are blue or grey. Here are the pantone colors that our company uses.

CORE COLOR
100c 91m 17y 6k 38r 58g 128b Hex #263A80 Pantone 7687 C

CORE CONTRAST COLOR
36c 29m 28y 0k 168r 168g 170b Hex #669999 Pantone Cool Gray 6C

I also attached some examples of what we have been looking at. Instead of green add the blue...instead of black maybe just be white.

Thank you

```html
<!DOCTYPE html>
<html lang="en">
<head>
<meta charset="utf-8">
<title>Nolan Reeves – Bio</title>
<link rel="stylesheet" href="https://fonts.googleapis.com/css2?family=Montserrat:wght@400;500;700&family=Open+Sans:wght@400;700&display=swap">
<style>
  :root {
    --core-blue: #263a80;
    --contrast-gray: #a8a8aa;
    --rule-gray: #c8c8c8;
    --body-gray: #6a6a6a;
    --ink: #333333;
    --paper: #ffffff;
    --backdrop: #e9e9ea;
  }
  * { margin: 0; padding: 0; box-sizing: border-box; }
  html, body {
    width: 991px; height: 1200px; overflow: hidden;
    background: var(--backdrop);
  }
  .bio-sheet {
    position: absolute; left: 68px; top: 0;
    width: 855px; height: 1200px;
    background: var(--paper);
    font-family: "Open Sans", Arial, sans-serif;
  }
  .accent-bar-left {
    position: absolute; left: 1px; top: 90px; width: 52px; height: 205px;
    background: var(--core-blue);
  }
  .headshot {
    position: absolute; left: 68px; top: 40px; width: 185px; height: 303px;
    border-radius: 48px;
    background: linear-gradient(180deg, #5a5a5c 0%, #3f3f42 45%, #23283a 100%);
  }
  .name-banner {
    position: absolute; left: 268px; top: 90px; width: 587px; height: 205px;
    background: var(--core-blue);
    color: #fff;
    font-family: "Montserrat", Arial, sans-serif;
  }
  .name-first, .name-last {
    position: absolute; left: 42px; font-size: 59px; line-height: 1; white-space: nowrap;
  }
  .name-first { top: 21px; font-weight: 700; }
  .name-last { top: 87px; font-weight: 400; }
  .name-rule {
    position: absolute; left: 38px; top: 150px; width: 363px; height: 1.5px; background: #fff;
  }
  .job-title {
    position: absolute; left: 38px; top: 163px;
    font-size: 22px; font-weight: 500; letter-spacing: 6.3px; white-space: nowrap;
  }
  .section-heading {
    position: absolute; left: 79px;
    color: var(--core-blue); font-weight: 700; line-height: 1;
  }
  .about-heading { top: 374px; font-size: 30px; }
  .about-rule {
    position: absolute; left: 79px; top: 413px; width: 703px; height: 2.5px; background: var(--rule-gray);
  }
  .about-text p {
    position: absolute; left: 79px; width: 703px;
    font-size: 11.6px; line-height: 18.1px; color: var(--body-gray);
    text-align: justify;
  }
  .contact-heading { top: 1016px; font-size: 34px; }
  .contact-rule {
    position: absolute; left: 79px; top: 1060px; width: 235px; height: 1.5px; background: var(--rule-gray);
  }
  .contact-item {
    position: absolute; font-size: 15px; color: var(--ink); white-space: nowrap; line-height: 1;
  }
  .brand-mark {
    position: absolute; left: 586px; top: 1040px; width: 183px; text-align: center;
    font-size: 46px; font-weight: 700; color: var(--core-blue); letter-spacing: 3px; line-height: 1;
  }
  .accent-corner-side {
    position: absolute; left: 825px; top: 847px; width: 30px; height: 353px; background: var(--core-blue);
  }
  .accent-corner-base {
    position: absolute; left: 69px; top: 1171px; width: 786px; height: 29px; background: var(--core-blue);
  }
</style>
</head>
<body>
<main class="bio-sheet">
  <div class="accent-bar-left"></div>
  <div class="headshot" role="img" aria-label="Head shot portrait of the marketing manager"></div>

  <header class="name-banner">
    <h1>
      <span class="name-first">NOLAN</span>
      <span class="name-last">REEVES</span>
    </h1>
    <div class="name-rule"></div>
    <p class="job-title">MARKETING MANAGER</p>
  </header>

  <h2 class="section-heading about-heading">About me</h2>
  <div class="about-rule"></div>
  <section class="about-text">
    <p style="top:423px">Lorem ipsum dolor sit amet, consectetuer adipiscing elit, sed diam nonummy nibh euismod tincidunt ut laoreet dolore magna aliquam erat volutpat. Ut wisi enim ad minim veniam, quis nostrud exerci tation ullamcorper suscipit lobortis nisl ut aliquip ex ea commodo consequat. Duis autem vel eum iriure dolor in hendrerit in vulputate velit esse molestie consequat, vel illum dolore eu feugiat nulla facilisis at vero eros et accumsan et iusto odio dignissim qui blandit praesent luptatum zzril delenit augue duis dolore te feugait nulla facilisi.</p>
    <p style="top:532px">Lorem ipsum dolor sit amet, cons ectetuer adipiscing elit, sed diam nonummy nibh euismod tincidunt ut laoreet dolore magna aliquam erat volutpat. Ut wisi enim ad minim veniam, quis nostrud exerci tation ullamcorper suscipit lobortis nisl ut aliquip ex ea commodo consequat. Lorem ipsum dolor sit amet, consectetuer adipiscing elit, sed diam nonummy nibh euismod tincidunt ut laoreet dolore magna aliquam erat volutpat. Ut wisi enim ad minim veniam, quis nostrud exerci tation ullamcorper suscipit lobortis nisl ut aliquip ex ea commodo consequat. Duis autem vel eum iriure dolor in hendrerit in vulputate velit esse molestie consequat, vel illum dolore eu feugiat nulla facilisis at vero eros et accumsan et iusto odio dignissim qui blandit praesent luptatum zzril delenit augue duis dolore te feugait nulla facilisi.</p>
    <p style="top:677px">Lorem ipsum dolor sit amet, cons ectetuer adipiscing elit, sed diam nonummy nibh euismod tincidunt ut laoreet dolore magna aliquam erat volutpat. Ut wisi enim ad minim veniam, quis nostrud exerci tation ullamcorper suscipit lobortis nisl ut aliquip ex ea commodo consequat.</p>
    <p style="top:750px">Lorem ipsum dolor sit amet, consectetuer adipiscing elit, sed diam nonummy nibh euismod tincidunt ut laoreet dolore magna aliquam erat volutpat. Ut wisi enim ad minim veniam, quis nostrud exerci tation ullamcorper suscipit lobortis nisl ut aliquip ex ea commodo consequat. Duis autem vel eum iriure dolor in hendrerit in vulputate velit esse molestie consequat, vel illum dolore eu feugiat nulla facilisis at vero eros et accumsan et iusto odio dignissim qui blandit praesent luptatum zzril delenit augue duis dolore te feugait nulla facilisi.</p>
    <p style="top:859px">Lorem ipsum dolor sit amet, cons ectetuer adipiscing elit, sed diam nonummy nibh euismod tincidunt ut laoreet dolore magna aliquam erat volutpat. Ut wisi enim ad minim veniam, quis nostrud exerci tation ullamcorper suscipit lobortis nisl ut aliquip ex ea commodo consequat. Lorem ipsum dolor sit amet, consectetuer adipiscing elit, sed diam nonummy nibh euismod tincidunt ut laoreet dolore magna aliquam erat volutpat. Ut wisi enim ad minim veniam, quis nostrud exerci tation ullamcorper suscipit lobortis nisl ut aliquip ex ea commodo consequat. Duis autem vel eum iriure dolor in hendrerit in vulputate velit esse molestie consequat, elit, sed diam nonummy nibh euismod.</p>
  </section>

  <h2 class="section-heading contact-heading">Contact</h2>
  <div class="contact-rule"></div>
  <address style="font-style:normal">
    <span class="contact-item" style="left:79px;top:1076px">Year, Month/Date</span>
    <span class="contact-item" style="left:80px;top:1110px">Your City, Country</span>
    <span class="contact-item" style="left:264px;top:1078px">123 - 456 -78</span>
    <span class="contact-item" style="left:264px;top:1110px">youremail@domain.com</span>
  </address>

  <div class="brand-mark">KVT</div>

  <div class="accent-corner-side"></div>
  <div class="accent-corner-base"></div>
</main>
</body>
</html>
```